House-share and Room Rental Website (With Focus on the Bedroom Landing Page)

Looking for website design for our House-share (executive accommodation) and room rental business.

Our company name is: Lodgivo could also be written as LodGivo or lodgivo. Either is fine .. just looking for a nice clean catchy logo to go with the design.

EXAMPLES
These are examples of other websites in this field that are doing well. this is a kind of baseline.
https://nestpartners-example.com.au/
https://www.bunkora-example.com/
https://www.dwelzy-example.com/
https://www.habiquo-example.net/
https://www.cohabiscout-example.com.au/

Our business model is to rent rooms to people looking for high-quality accommodation. We fill the gap between those looking to rent rooms and those with rooms to rent. However, our model is slightly different from those already on the market as we looking to fill a massive gap in the market delivering upmarket rooms for rent.(Executive Accommodation) also in the back end will be coupled with a self management process in the back end.

We offer executive style accommodation that stands out above the rest. With special extras like fire safety.. and management processes that create happier homes. We are looking for a web design package that can help us grow and scale our business. We need a design that is captivating

Our MAIN focus is having a room landing page that stands out from the rest... The core of our business will rely on the promotion of the rooms in a share house... so the whole design relies on the BEDROOM landing page to drive results.

Target Market(s)

We have 2 markets we are aiming at ... the first market is people offering rooms to rent who want the highest rental return. The second market is people looking to rent safe, high-quality rooms, in houses that are well managed and looked after.

Industry/Entity Type

Share Economy

Logo Text

LodGivo

Number of Pages Required

5+ page

Font styles to use
Sans Serif

Colors
3276b5

Requirements
Must have
• A messaging system whereby we can create direct communication between those offering rooms and those looking for rooms.
• A call to action that says " Schedule an Inspection"
• Landing page for promoting rooms
• A home page for showing stock.
• Profile page for those selling rooms
• Profile page for those looking for rooms.
• A scheduling calendar for booking inspections
Nice to have
• Pages where new residents can lock in a room.. pay bond and rents.. and sign contracts
• Notifications
• SMS capabilities in the backend.
Should not have
• No script or handwriting fonts.

```html
<!DOCTYPE html>
<html lang="en">
<head>
<meta charset="utf-8">
<title>LodGivo – The white room</title>
<link rel="stylesheet" href="https://fonts.googleapis.com/css2?family=Lato:wght@300;400;700;900&display=swap">
<style>
:root{
  --brand:#3276b5;
  --ink:#1f1f1f;
  --muted:#8a8a8a;
  --faint:#c8c8c8;
  --line:#d9d9d9;
  --bg:#ffffff;
}
*{box-sizing:border-box;margin:0;padding:0}
html,body{width:880px;height:1200px;overflow:hidden;background:var(--bg)}
body{position:relative;font-family:'Lato',sans-serif;color:var(--ink)}
.abs{position:absolute}
.brand{left:22px;top:25px;display:flex;align-items:center;gap:6px;font-size:15px;font-weight:700;color:var(--brand)}
.brand-square{width:10px;height:10px;background:var(--brand)}
.nav-item{top:27px;font-size:8px;font-weight:700;letter-spacing:.6px}
.nav-sep{top:26px;font-size:8px}
.sign-in{left:796px;top:19px;width:62px;height:23px;border:1px solid var(--ink);color:var(--brand);font-size:8px;font-weight:700;letter-spacing:.6px;display:flex;align-items:center;justify-content:center}
.photo{background:linear-gradient(165deg,#ecebe8,#dcd8d2 45%,#f1f0ee 75%,#d6d2cc)}
.photo.soft{background:linear-gradient(160deg,#e6e3df,#cfcac4 50%,#ebe9e6)}
.photo.vase{background:linear-gradient(175deg,#f2f2f0,#dadad6 65%,#4a4541 90%,#f4f4f2)}
.city{font-size:10px;font-weight:700;letter-spacing:.2px}
.room-title{font-size:29px;font-weight:300;line-height:1;white-space:nowrap}
.room-type{font-size:15px;font-weight:900;letter-spacing:-.2px}
.rating{display:flex;align-items:center;gap:2px;font-size:9px}
.rating svg{width:10px;height:10px}
.description{font-size:11px;line-height:14.6px;width:318px;letter-spacing:-.1px}
.price-label{font-size:8px}
.price{font-size:26px;font-weight:700;color:var(--brand)}
.cta{left:600px;top:425px;width:126px;height:22px;background:var(--brand);color:#fff;font-size:8px;letter-spacing:.5px;display:flex;align-items:center;justify-content:center;white-space:nowrap}
.facts{left:488px;top:490px;width:244px;display:grid;grid-template-columns:repeat(5,1fr);row-gap:14px;text-align:center}
.fact svg{width:14px;height:14px;stroke:var(--ink);fill:none;stroke-width:1.1}
.fact small{display:block;font-size:3.5px;color:var(--faint);text-transform:uppercase;margin-top:1px}
.fact span{display:block;font-size:7.2px}
h2{font-size:15px;font-weight:900}
.amenities{left:153px;top:614px;width:576px;display:flex;justify-content:space-between}
.amenity{text-align:center;font-size:9.5px}
.amenity svg{width:30px;height:26px;stroke:var(--ink);fill:none;stroke-width:1.1;display:block;margin:0 auto 7px}
.transport li{list-style:none;display:flex;align-items:center;font-size:9.5px;font-weight:700;width:140px}
.transport svg{width:16px;height:14px;stroke:var(--ink);fill:none;stroke-width:1.1;margin-right:9px}
.transport .chev{width:8px;height:8px;margin:0 0 0 auto}
.map{left:446px;top:705px;width:281px;height:144px;background:linear-gradient(135deg,#eeeeec,#e7e6e2 60%,#dce8cc)}
.card{width:183px}
.card .photo{height:103px}
.card .city{color:var(--brand);font-weight:400;margin-top:12px;font-size:9px}
.card .title{font-size:17px;font-weight:300;margin-top:5px;line-height:1.1;white-space:nowrap}
.card .room-type{font-size:12px}
.footer-rule{left:153px;top:1120px;width:574px;height:1px;background:var(--line)}
.footer-brand{left:153px;top:1130px;display:flex;align-items:center;gap:6px;font-size:14px;font-weight:700;color:var(--muted)}
.footer-brand .brand-square{background:var(--muted)}
.footer-col{top:1129px;font-size:11px;color:var(--muted);line-height:18.5px;list-style:none}
</style>
</head>
<body>
<svg width="0" height="0" style="position:absolute">
  <defs>
    <symbol id="star" viewBox="0 0 24 24"><path d="M12 2l2.9 6.9 7.1.6-5.4 4.7 1.7 7.3L12 17.7 5.7 21.5l1.7-7.3L2 9.5l7.1-.6z"/></symbol>
  </defs>
</svg>

<header class="site-header">
  <div class="abs brand"><span class="brand-square"></span>LodGivo</div>
  <nav>
    <span class="abs nav-item" style="left:495px">BROWSE</span>
    <span class="abs nav-item" style="left:553px">DISCOVER</span>
    <span class="abs nav-sep" style="left:620px">I</span>
    <span class="abs nav-item" style="left:641px">LIST YOUR FLAT</span>
    <span class="abs nav-sep" style="left:732px">I</span>
    <span class="abs nav-item" style="left:754px">LOGIN</span>
  </nav>
  <div class="abs sign-in">SIGN IN</div>
</header>

<section class="gallery">
  <div class="abs photo" style="left:12px;top:66px;width:471px;height:324px" role="img" aria-label="White bedroom with pillows, breakfast tray and flower vase on the bed"></div>
  <div class="abs photo soft" style="left:495px;top:66px;width:373px;height:156px" role="img" aria-label="Close-up of pillows and a wooden tray with flowers"></div>
  <div class="abs photo vase" style="left:495px;top:234px;width:183px;height:156px" role="img" aria-label="Grey ceramic ring vase on a bedside table"></div>
  <div class="abs photo soft" style="left:690px;top:234px;width:178px;height:156px" role="img" aria-label="Quilted white pillows on the bed"></div>
</section>

<section class="room-summary">
  <div class="abs city" style="left:153px;top:411px">MELBOURNE</div>
  <h1 class="abs room-title" style="left:152px;top:427px">The white room</h1>
  <div class="abs room-type" style="left:153px;top:460px">DOUBLE BEDROOM</div>
  <div class="abs rating" style="left:153px;top:484px;color:var(--brand)">
    <svg fill="currentColor"><use href="#star"/></svg><svg fill="currentColor"><use href="#star"/></svg><svg fill="currentColor"><use href="#star"/></svg><svg fill="currentColor"><use href="#star"/></svg><svg fill="currentColor"><use href="#star"/></svg><span style="color:var(--ink);margin-left:2px">314</span>
  </div>
  <p class="abs description" style="left:153px;top:500px">Maecenas et ligula consectetur diam convallis posuere eget eget velit. Morbi ac augue at dolor sollicitudin rhoncus. Cras vulputate, metus at iaculis varius, tellus nisl scelerisque magna, vel consectetur elit mi id nisi. Ut blandit orci vel lectus sagittis, nec fermentum neque fringilla.</p>

  <div class="abs price-label" style="left:495px;top:412px">Rental price (per month)</div>
  <div class="abs price" style="left:494px;top:422px">A$600</div>
  <div class="abs cta">SCHEDULE AN INSPECTION</div>

  <div class="abs facts">
    <div class="fact"><svg viewBox="0 0 16 16"><circle cx="8" cy="5" r="3"/><path d="M2 15c0-4 3-6 6-6s6 2 6 6"/></svg><small>Gender</small><span>Single</span></div>
    <div class="fact"><svg viewBox="0 0 16 16"><rect x="4" y="2" width="8" height="12"/><path d="M3 2h10"/></svg><small>Room size</small><span>40 Sqm</span></div>
    <div class="fact"><svg viewBox="0 0 16 16"><path d="M3 2v6h10v2c0 2-2 3-4 3H6l-1 2M3 5h4"/></svg><small>Bathroom</small><span>Private</span></div>
    <div class="fact"><svg viewBox="0 0 16 16"><rect x="2" y="2" width="12" height="12"/><path d="M6 12V5h3a2 2 0 010 4H6"/></svg><small>Parking</small><span>Private</span></div>
    <div class="fact"><svg viewBox="0 0 16 16"><circle cx="8" cy="8" r="6"/><path d="M4 12l8-8M5 9h6"/></svg><small>Smoking</small><span>Not allowed</span></div>
    <div class="fact"><svg viewBox="0 0 16 16"><path d="M12 9v5H2V4h5M10 2l3 3-6 6H4V8z"/></svg><small>Contract</small><span>3 months</span></div>
    <div class="fact"><svg viewBox="0 0 16 16"><path d="M2 14V4h12v10M2 10h12M4 8V6h8v2"/></svg><small>Bed size</small><span>200x200</span></div>
    <div class="fact"><svg viewBox="0 0 16 16"><circle cx="5" cy="5" r="2.5"/><circle cx="11" cy="5" r="2.5"/><path d="M1 13c0-3 2-4.5 4-4.5s4 1.5 4 4.5M7 13c0-3 2-4.5 4-4.5s4 1.5 4 4.5"/></svg><small>Housemates</small><span>Professionals</span></div>
    <div class="fact"><svg viewBox="0 0 16 16"><rect x="5" y="1" width="6" height="14"/><path d="M9 8h.5"/></svg><small>Room type</small><span>Private</span></div>
    <div class="fact"><svg viewBox="0 0 16 16"><path d="M2 7c3.5-3 8.5-3 12 0M4.5 9.5c2-1.7 5-1.7 7 0M7 12c.6-.4 1.4-.4 2 0"/></svg><small>Internet</small><span>600mbps</span></div>
  </div>
</section>

<section class="amenities-section">
  <h2 class="abs" style="left:153px;top:588px">Amenities</h2>
  <div class="abs amenities">
    <div class="amenity"><svg viewBox="0 0 30 26"><path d="M3 20V11h24v9M6 11V6h18v5M3 20h24M5 20v3M25 20v3M3 15h24"/></svg>Furnished</div>
    <div class="amenity"><svg viewBox="0 0 30 26"><rect x="3" y="3" width="24" height="17" rx="4"/><path d="M11 23h8M10 8h5M12.5 8v7M16 8l2 7 2-7"/></svg>SmartTV</div>
    <div class="amenity"><svg viewBox="0 0 30 26"><rect x="7" y="2" width="16" height="22"/><path d="M7 9h16M7 16h16M10 5h3M10 12h3M10 19h3"/></svg>Storage space</div>
    <div class="amenity"><svg viewBox="0 0 30 26"><path d="M3 14h24M5 14v10M25 14v10M16 14v10h9M16 19h9M6 4l2 4h-3M7 8v6M19 6h6v6h-6zM22 12v2"/></svg>Workstation</div>
    <div class="amenity"><svg viewBox="0 0 30 26"><rect x="5" y="2" width="20" height="22"/><path d="M15 2v22M5 8h10M8 4v3M10 4v3M17 11h6M17 15h6"/></svg>Wardrobe</div>
    <div class="amenity"><svg viewBox="0 0 30 26"><path d="M4 14h22v3c0 3-3 5-6 5h-10c-3 0-6-2-6-5zM8 14v-4h5v4M22 14V4h-4v3M17 9l1 1M19 9v2"/></svg>Ensuite shower</div>
    <div class="amenity"><svg viewBox="0 0 30 26"><path d="M3 12h24v12H3zM15 12v12M6 15h6v6H6zM18 15h6M3 4h24M7 4v4M15 4v4M23 4v4M5 8h4M13 8h4M21 8h4"/></svg>Kitchenette</div>
  </div>
</section>

<section class="public-amenities">
  <h2 class="abs" style="left:153px;top:679px">Public Amenities</h2>
  <div class="abs" style="left:153px;top:705px;display:flex">
    <svg viewBox="0 0 20 14" style="width:20px;height:14px;stroke:var(--ink);fill:none;stroke-width:1;margin-right:6px"><path d="M2 7h15a1.2 1.2 0 010 2H2zM8 7L6 2h2l4 5M8 9l-2 4h2l4-4M2 7L1 4h1.5l1.5 3"/></svg>
    <div><div style="font-size:9.5px;font-weight:700">Distance to the airport</div><div style="font-size:7.5px;margin-top:5px">15 minutes by car</div></div>
  </div>
  <ul class="abs transport" style="left:153px;top:744px">
    <li><svg viewBox="0 0 16 14"><rect x="3" y="1" width="10" height="11" rx="1"/><path d="M3 6h10M5 12v2M11 12v2M5 9h1M10 9h1"/></svg>Busses<svg class="chev" viewBox="0 0 8 8"><path d="M1 2.5l3 3 3-3"/></svg></li>
    <li style="margin-top:10px"><svg viewBox="0 0 16 14"><rect x="2" y="1" width="12" height="10" rx="1"/><path d="M2 7h12M4 11l-2 3M12 11l2 3"/></svg>Trains<svg class="chev" viewBox="0 0 8 8"><path d="M1 2.5l3 3 3-3"/></svg></li>
    <li style="margin-top:10px"><svg viewBox="0 0 16 14"><path d="M2 11V7l2-4h8l2 4v4zM2 7h12M3 11v2M13 11v2M4 9h1M11 9h1"/></svg>Rent a car<svg class="chev" viewBox="0 0 8 8"><path d="M1 2.5l3 3 3-3"/></svg></li>
  </ul>
</section>

<section class="location">
  <h2 class="abs" style="left:446px;top:679px">Location</h2>
  <div class="abs" style="left:538px;top:681px;font-size:10.5px">Marlow Crescent, BRIARWOOD HEIGHTS</div>
  <div class="abs map" role="img" aria-label="Street map of the neighbourhood with the room location marked"></div>
  <svg class="abs" style="left:604px;top:773px;width:10px;height:14px" viewBox="0 0 10 14"><path d="M5 14S0 8 0 5a5 5 0 0110 0c0 3-5 9-5 9z" fill="#b0283a"/><circle cx="5" cy="5" r="1.6" fill="#fff"/></svg>
</section>

<section class="similar">
  <h2 class="abs" style="left:153px;top:869px">Similar Bedrooms</h2>
  <article class="abs card" style="left:153px;top:896px">
    <div class="photo" style="background:linear-gradient(160deg,#6b5a3e,#c4a77a 55%,#5a5a3c)" role="img" aria-label="Warm-lit hotel style bedroom with olive bedspread"></div>
    <div class="city">MELBOURNE</div>
    <div class="title">Luxury in the mountains</div>
    <div class="room-type">DOUBLE BEDROOM</div>
    <div class="rating" style="color:var(--brand);margin-top:2px"><svg fill="currentColor"><use href="#star"/></svg><svg fill="currentColor"><use href="#star"/></svg><svg fill="currentColor"><use href="#star"/></svg><svg fill="currentColor"><use href="#star"/></svg><svg fill="#cfcfcf"><use href="#star"/></svg><span style="color:var(--ink);margin-left:4px">180</span></div>
  </article>
  <article class="abs card" style="left:348px;top:896px">
    <div class="photo" style="background:linear-gradient(170deg,#4a2a2a,#8a5a50 45%,#d8d4d0 70%,#6a6a70)" role="img" aria-label="Dark red bedroom with white bed and patterned runner"></div>
    <div class="city">MELBOURNE</div>
    <div class="title">Cherry room</div>
    <div class="room-type">DOUBLE BEDROOM</div>
    <div class="rating" style="color:var(--brand);margin-top:2px"><svg fill="currentColor"><use href="#star"/></svg><svg fill="currentColor"><use href="#star"/></svg><svg fill="currentColor"><use href="#star"/></svg><svg fill="currentColor"><use href="#star"/></svg><svg fill="currentColor" style="opacity:.55"><use href="#star"/></svg><span style="color:var(--ink);margin-left:4px">215</span></div>
  </article>
  <article class="abs card" style="left:544px;top:896px">
    <div class="photo" style="background:linear-gradient(175deg,#4d4944,#8b857c 55%,#5876a8 80%,#d9d6d0)" role="img" aria-label="Bedroom with stone feature wall and blue bedspread"></div>
    <div class="city">MELBOURNE</div>
    <div class="title">The wall</div>
    <div class="room-type">DOUBLE BEDROOM</div>
    <div class="rating" style="color:var(--brand);margin-top:2px"><svg fill="currentColor"><use href="#star"/></svg><svg fill="currentColor"><use href="#star"/></svg><svg fill="currentColor"><use href="#star"/></svg><svg fill="currentColor"><use href="#star"/></svg><svg fill="currentColor"><use href="#star"/></svg><span style="color:var(--ink);margin-left:4px">432</span></div>
  </article>
</section>

<footer class="site-footer">
  <div class="abs footer-rule"></div>
  <div class="abs footer-brand"><span class="brand-square"></span>LodGivo</div>
  <ul class="abs footer-col" style="left:299px"><li>Paid methods</li><li>Cancellation policy</li><li>Other</li></ul>
  <ul class="abs footer-col" style="left:446px"><li>Conditions</li><li>Be a Landlor</li><li>Selling rooms</li></ul>
  <ul class="abs footer-col" style="left:593px"><li>Terms</li><li>Privacity</li><li>Sitemap</li></ul>
</footer>
</body>
</html>
```